BOLD & MINIMALIST DESIGN NEEDED

We want a very bold but minimalistic business card design that is impactful and utilizes both sides of the business card. Our current logo is included for your use.

We want bold fonts and good use of negative space. We don't want the logo to overpower the design.

Target Market(s)

Professionals who are building new commercial buildings.

Industry/Entity Type

Construction

Contact Information for Business Card

Name, Title, email, office phone, cell phone, website

Font styles to use
Serif
Sans Serif

Requirements
Must have
• Bold design!

```html
<!DOCTYPE html>
<html lang="en">
<head>
<meta charset="utf-8">
<title>Ridgecrest Business Card</title>
<link rel="stylesheet" href="https://fonts.googleapis.com/css2?family=Roboto:wght@400;700&display=swap">
<style>
  :root {
    --page: #e9e7e3;
    --card-white: #ffffff;
    --card-black: #1b1b1c;
    --ink: #1a1a1a;
    --ink-soft: #3a3a3a;
    --rule: #4a4a4a;
    --green: #8cc63f;
    --pattern-top: #2a2a2b;
    --pattern-bottom: #141415;
  }
  * { box-sizing: border-box; margin: 0; padding: 0; }
  html, body {
    width: 1200px; height: 931px; overflow: hidden;
    background: var(--page);
    font-family: "Roboto", Arial, sans-serif;
  }
  .stage { position: relative; width: 1200px; height: 931px; }

  .card {
    position: absolute;
    width: 560px; height: 320px;
    border-radius: 18px;
    overflow: hidden;
    box-shadow: 0 10px 24px rgba(0,0,0,.18);
  }

  /* Back side */
  .card-back { left: 70px; top: 90px; background: var(--card-black); }
  .back-pattern {
    position: absolute; inset: 0;
    background: linear-gradient(160deg, var(--pattern-top), var(--pattern-bottom));
  }
  .back-brand {
    position: absolute; left: 0; right: 0; top: 50%;
    transform: translateY(-50%);
    display: flex; align-items: center; justify-content: center; gap: 10px;
  }
  .brand-square { width: 18px; height: 18px; background: var(--green); }
  .back-brand .brand-name { color: #fff; font-size: 26px; }
  .brand-name { font-weight: 700; letter-spacing: 1px; }

  /* Front side */
  .card-front { left: 570px; top: 510px; background: var(--card-white); }
  .front-brand {
    position: absolute; right: 40px; top: 52px;
    display: flex; align-items: center; gap: 12px;
  }
  .front-brand .brand-square { width: 24px; height: 24px; }
  .front-brand .brand-name { color: var(--ink); font-size: 36px; }

  .person { position: absolute; left: 40px; top: 168px; }
  .person-name { color: var(--green); font-weight: 700; font-size: 26px; line-height: 1.1; }
  .person-title { color: var(--ink-soft); font-size: 17px; margin-top: 4px; }

  .divider {
    position: absolute; left: 40px; right: 40px; top: 234px;
    height: 1px; background: var(--rule);
  }

  .contact { position: absolute; top: 248px; font-size: 13.5px; color: var(--ink-soft); }
  .contact li { list-style: none; display: flex; align-items: center; gap: 7px; height: 22px; }
  .contact svg { width: 14px; height: 14px; fill: var(--ink); flex: none; }
  .contact-phones { left: 40px; }
  .contact-online { left: 220px; }
  .contact-address { right: 40px; text-align: right; }
  .contact-address li { justify-content: flex-end; }

  .bottom-band { position: absolute; left: 0; bottom: 0; width: 560px; height: 14px; }
</style>
</head>
<body>
<main class="stage">

  <section class="card card-back" aria-label="Card back">
    <div class="back-pattern" role="img" aria-label="Repeating embossed brand pattern in dark grey"></div>
    <div class="back-brand">
      <span class="brand-square"></span>
      <span class="brand-name">RIDGECREST</span>
    </div>
  </section>

  <section class="card card-front" aria-label="Card front">
    <div class="front-brand">
      <span class="brand-square"></span>
      <span class="brand-name">RIDGECREST</span>
    </div>

    <div class="person">
      <p class="person-name">Jonathan Smith</p>
      <p class="person-title">Owner</p>
    </div>

    <div class="divider"></div>

    <ul class="contact contact-phones">
      <li>
        <svg viewBox="0 0 24 24"><path d="M6.6 10.8a15.1 15.1 0 0 0 6.6 6.6l2.2-2.2c.3-.3.7-.4 1-.2 1.1.4 2.3.6 3.6.6.6 0 1 .4 1 1V20c0 .6-.4 1-1 1A17 17 0 0 1 3 4c0-.6.4-1 1-1h3.5c.6 0 1 .4 1 1 0 1.3.2 2.5.6 3.6.1.3 0 .7-.2 1z"/></svg>
        <span>044-123 456 789</span>
      </li>
      <li>
        <svg viewBox="0 0 24 24"><path d="M3 9c0-2 4-4 9-4s9 2 9 4v2h-5V9H8v2H3zM6 12h12l2 8H4zm6 2a2.5 2.5 0 1 0 0 5 2.5 2.5 0 0 0 0-5z"/></svg>
        <span>044-123 456 789</span>
      </li>
    </ul>

    <ul class="contact contact-online">
      <li>
        <svg viewBox="0 0 24 24"><path d="M2 5h20v14H2zm2 2v.5l8 5.5 8-5.5V7z"/></svg>
        <span>info@webname.com</span>
      </li>
      <li>
        <svg viewBox="0 0 24 24"><path d="M12 2a10 10 0 1 0 0 20 10 10 0 0 0 0-20zm0 2a8 8 0 0 1 6.9 4H15l-1 2-3-1-1 3 3 2-1 4-2-1V13L7 11V8l2-2V4.3A8 8 0 0 1 12 4z"/></svg>
        <span>www.website.com</span>
      </li>
    </ul>

    <ul class="contact contact-address">
      <li>Address line goes here</li>
      <li>45452, Country name</li>
    </ul>

    <svg class="bottom-band" viewBox="0 0 560 14" aria-hidden="true">
      <rect x="0" y="8" width="330" height="6" fill="#1a1a1a"/>
      <polygon points="318,0 560,0 560,14 330,14" fill="#8cc63f"/>
    </svg>
  </section>

</main>
</body>
</html>
```